New Webpage for High Class Expert Witness Services Company

We are looking for a minimalist design for a webpage that just has our logo and an entry form offer to connect with one of our Liaisons.
The entry form should just ask for Name, Email, Contact Info and Description of Project.

Company Name is: The Marlowe Crest Advisory Services

Number of Pages Required

1 page

```html
<!DOCTYPE html>
<html lang="en">
<head>
<meta charset="utf-8">
<title>Connect with a Liaison – The Marlowe Crest Advisory Services</title>
<link rel="stylesheet" href="https://fonts.googleapis.com/css2?family=Playfair+Display:wght@400;700&family=Roboto:wght@400&display=swap">
<style>
  :root {
    --page-bg: #131313;
    --panel-bg: #0e0e0e;
    --heading: #d2d2d2;
    --text: #ffffff;
    --label: #ffffff;
    --field-bg: #ffffff;
    --placeholder: #9a9a9a;
    --form-border: #a9a9a9;
    --button-bg: #c4c4c4;
    --button-text: #1a1a1a;
    --footer-text: #d0d0d0;
    --below: #ffffff;
  }
  * { box-sizing: border-box; margin: 0; padding: 0; }
  html, body {
    width: 1200px;
    height: 1019px;
    overflow: hidden;
    background: var(--below);
  }
  .page {
    width: 1200px;
    height: 992px;
    background: var(--page-bg);
    padding-top: 8px;
  }
  .content {
    width: 540px;
    margin: 0 auto;
  }
  .brand-panel {
    height: 260px;
    background: var(--panel-bg);
    display: flex;
    align-items: center;
    justify-content: center;
    gap: 12px;
  }
  .brand-mark {
    width: 22px;
    height: 22px;
    background: #cfcfcf;
  }
  .brand-name {
    font-family: "Playfair Display", serif;
    font-weight: 400;
    font-size: 22px;
    letter-spacing: 1.5px;
    text-transform: uppercase;
    color: #cfcfcf;
  }
  .intro-title {
    margin-top: 11px;
    font-family: "Playfair Display", serif;
    font-weight: 400;
    font-size: 28px;
    line-height: 36px;
    text-align: center;
    color: var(--heading);
    letter-spacing: -0.3px;
  }
  .intro-text {
    margin-top: 12px;
    font-family: "Roboto", sans-serif;
    font-size: 13.2px;
    line-height: 20.5px;
    text-align: justify;
    color: var(--text);
  }
  .liaison-form {
    margin-top: 32px;
    height: 398px;
    border: 1px solid var(--form-border);
    border-radius: 19px;
    padding: 28px 29px 0;
  }
  .field-label {
    display: block;
    font-family: "Playfair Display", serif;
    font-weight: 700;
    font-size: 13px;
    line-height: 16px;
    color: var(--label);
    text-transform: uppercase;
    margin-bottom: 7px;
  }
  .field-input, .field-textarea {
    display: block;
    width: 100%;
    height: 33px;
    border: none;
    border-radius: 3px;
    background: var(--field-bg);
    padding: 0 14px;
    font-family: "Roboto", sans-serif;
    font-size: 12px;
    color: #222;
    margin-bottom: 8px;
  }
  .field-textarea {
    height: 80px;
    padding: 6px 12px;
    resize: vertical;
  }
  .field-input::placeholder, .field-textarea::placeholder { color: var(--placeholder); }
  .submit-button {
    display: block;
    width: 100%;
    height: 33px;
    margin-top: 1px;
    border: none;
    border-radius: 3px;
    background: var(--button-bg);
    color: var(--button-text);
    font-family: "Playfair Display", serif;
    font-size: 13px;
    text-transform: uppercase;
  }
  .site-footer {
    margin-top: 60px;
    text-align: center;
    font-family: "Playfair Display", serif;
    font-variant: small-caps;
    font-size: 15px;
    color: var(--footer-text);
  }
</style>
</head>
<body>
  <div class="page">
    <main class="content">
      <header class="brand-panel">
        <span class="brand-mark"></span>
        <span class="brand-name">Marlowe Crest Advisory Services</span>
      </header>

      <h1 class="intro-title">CONNECT WITH ONE OF OUR LIAISONS</h1>
      <p class="intro-text">Lorem ipsum dolor sit amet, consectetur adipiscing elit, sed do eiusmod tempor incididunt ut labore et dolore magna aliqua. Vulputate dignissim suspendisse in est ante. Faucibus turpis in eu mi bibendum neque. Sodales ut etiam sit amet nisl purus. Velit laoreet id donec ultrices tincidunt.</p>

      <form class="liaison-form">
        <label class="field-label" for="name">Name</label>
        <input class="field-input" id="name" type="text" placeholder="Name">

        <label class="field-label" for="email">Email</label>
        <input class="field-input" id="email" type="email" placeholder="Type your Email">

        <label class="field-label" for="contact">Contact Info</label>
        <input class="field-input" id="contact" type="text" placeholder="Type your contact information">

        <label class="field-label" for="project">Description of Project</label>
        <textarea class="field-textarea" id="project" placeholder="Describe about your project."></textarea>

        <button class="submit-button" type="submit">Submit</button>
      </form>

      <footer class="site-footer">Copyright © 2026 &amp; Powered by The Marlowe Crest Advisory Services</footer>
    </main>
  </div>
</body>
</html>
```